Business card design needed

I would like a one sided black business card with the information provided above. Refer to my website www.brightvolleyracquets.com.au for an example of colors I have used for my site, would like to keep this consistent for my business cards also, I will upload my logo below.

I am a new small business that provides tennis customers with racquet re stringing, tennis strings and accessories.

Industry/Entity Type

Small Business

Contact Information for Business Card

Bright Volley Tennis

Owen Whitby
Managing Director

brightvolleyracquets@mailbox.example
www.brightvolleyracquets.com.au
0491 726 305

Racquet Restringing/Tennis Strings/Accessories

Requirements
Must have
• Must have my logo and card must be black

```html
<!DOCTYPE html>
<html lang="en">
<head>
<meta charset="utf-8">
<title>Bright Volley Tennis – Business Card</title>
<link href="https://fonts.googleapis.com/css2?family=Open+Sans:wght@400;600;700&display=swap" rel="stylesheet">
<style>
  :root {
    --backdrop: #5b4331;
    --card-black: #050505;
    --lime: #b7d432;
    --ink-light: #e6e6e6;
    --ink-dark: #1a1a1a;
    --navy-glow: #1c2740;
  }
  * { box-sizing: border-box; margin: 0; padding: 0; }
  html, body {
    width: 1200px; height: 475px; overflow: hidden;
    background: var(--backdrop);
    font-family: "Open Sans", Arial, sans-serif;
  }
  .canvas { position: relative; width: 1200px; height: 475px; }

  .card {
    position: absolute; top: 86px;
    width: 547px; height: 313px;
    background: var(--card-black);
    border-radius: 14px;
    overflow: hidden;
  }
  .card--front { left: 27px; }
  .card--back { left: 606px; }

  .brand {
    position: absolute;
    display: flex; align-items: center; gap: 10px;
    color: var(--lime);
    font-weight: 700;
    white-space: nowrap;
  }
  .brand__dot {
    width: 26px; height: 26px; border-radius: 50%;
    background: var(--lime);
    flex: none;
  }
  .card--front .brand { left: 62px; top: 78px; font-size: 27px; }
  .card--back .brand { left: 50%; top: 118px; transform: translateX(-50%); font-size: 31px; }
  .card--back .brand__dot { width: 30px; height: 30px; }

  .brand-watermark {
    position: absolute; left: 350px; top: 8px;
    width: 190px; height: 250px;
    background: radial-gradient(ellipse at 45% 40%, var(--navy-glow) 0%, rgba(5,5,5,0) 70%);
  }

  .contact-list {
    position: absolute; left: 60px; top: 188px;
    list-style: none;
  }
  .contact-list li {
    display: flex; align-items: center; gap: 10px;
    height: 20px;
    color: var(--ink-light);
    font-size: 13.5px;
  }
  .contact-list svg { width: 12px; height: 12px; flex: none; }

  .rule-line {
    position: absolute; left: 0; right: 0; top: 270px;
    height: 3px; background: var(--lime);
  }
  .name-band {
    position: absolute; left: 0; right: 0; top: 277px; bottom: 0;
    background: var(--lime);
    display: flex; align-items: baseline;
    padding: 8px 0 0 66px;
    color: var(--ink-dark);
  }
  .name-band .person { font-size: 17px; letter-spacing: 0.3px; text-transform: uppercase; }
  .name-band .role { font-size: 13px; margin-left: 5px; }

  .web-line {
    position: absolute; left: 0; right: 0; top: 250px;
    text-align: center;
    color: var(--ink-light);
    font-size: 13px; letter-spacing: 2.4px;
  }
</style>
</head>
<body>
<div class="canvas">

  <section class="card card--front">
    <div class="brand-watermark" role="img" aria-label="Faint large brand decoration"></div>
    <div class="brand"><span class="brand__dot"></span>Bright Volley Tennis</div>

    <ul class="contact-list">
      <li>
        <svg viewBox="0 0 12 12" aria-hidden="true"><path d="M3 1l2 2.5-1.2 1.2a7 7 0 0 0 3.5 3.5L8.5 7 11 9l-1.3 1.8C5.5 11 1 6.5 1.2 2.3z" fill="var(--lime)"/></svg>
        0491 726 305
      </li>
      <li>
        <svg viewBox="0 0 12 12" aria-hidden="true"><rect x="1" y="3" width="10" height="7" fill="var(--lime)"/><path d="M1 3l5 4 5-4" stroke="#050505" stroke-width="1" fill="none"/></svg>
        brightvolleyracquets@mailbox.example
      </li>
      <li>
        <svg viewBox="0 0 12 12" aria-hidden="true"><g fill="none" stroke="var(--lime)" stroke-width="1"><circle cx="6" cy="6" r="5"/><ellipse cx="6" cy="6" rx="2.2" ry="5"/><path d="M1 6h10M2 3.5h8M2 8.5h8"/></g></svg>
        www.brightvolleyracquets.com.au
      </li>
    </ul>

    <div class="rule-line"></div>
    <div class="name-band">
      <span class="person">Owen Whitby,</span>
      <span class="role">Managing Director</span>
    </div>
  </section>

  <section class="card card--back">
    <div class="brand"><span class="brand__dot"></span>Bright Volley Tennis</div>
    <p class="web-line">www.brightvolleyracquets.com.au</p>
  </section>

</div>
</body>
</html>
```